Business card for a new cabinet shop company named Veloran Cabinets for high end cabinets

Design a business card, thinking dark rich green with colours to speak of high end luxury ie; cream, gold, black possibly

Mitchell Tarrowby
Director Craftsman
Email: info@veloranjoinery-example.com.au
Instagram : @veloran.cabinets

```html
<!DOCTYPE html>
<html lang="en">
<head>
<meta charset="utf-8">
<title>Veloran Cabinets – Business Card</title>
<link rel="stylesheet" href="https://fonts.googleapis.com/css2?family=Arimo:wght@400;700&display=swap">
<style>
  :root {
    --backdrop: #dcdcdc;
    --card-white: #ffffff;
    --gold: #c9a95f;
    --gold-light: #d9bd7a;
    --gold-deep: #c2a258;
    --ink: #3a3a3a;
    --ink-soft: #5a5a5a;
    --divider: #bdbdbd;
    --white: #ffffff;
  }
  * { margin: 0; padding: 0; box-sizing: border-box; }
  html, body { width: 1200px; height: 1200px; overflow: hidden; }
  body {
    background: var(--backdrop);
    font-family: "Arimo", Arial, sans-serif;
    position: relative;
  }
  .card {
    position: absolute;
    left: 256px;
    width: 688px;
    height: 393px;
    border-radius: 21px;
    overflow: hidden;
  }
  .card-front { top: 159px; background: var(--card-white); }
  .card-back { top: 653px; background: var(--gold); }

  .front-brand {
    position: absolute;
    left: 62px;
    top: 150px;
    width: 262px;
    height: 69px;
    display: flex;
    align-items: center;
    gap: 12px;
  }
  .brand-dot {
    width: 14px; height: 14px;
    background: var(--gold);
    border-radius: 50%;
    flex: none;
  }
  .brand-name {
    font-size: 24px;
    font-weight: 400;
    color: var(--ink);
    letter-spacing: 0.5px;
    white-space: nowrap;
  }
  .front-divider {
    position: absolute;
    left: 343px;
    top: 124px;
    width: 1px;
    height: 137px;
    background: var(--divider);
  }
  .person {
    position: absolute;
    left: 369px;
    top: 124px;
  }
  .person-name {
    font-size: 26px;
    font-weight: 700;
    color: var(--gold);
    line-height: 30px;
  }
  .person-role {
    font-size: 15px;
    color: var(--ink-soft);
    line-height: 20px;
  }
  .contacts {
    position: absolute;
    left: 369px;
    top: 194px;
    list-style: none;
  }
  .contacts li {
    display: flex;
    align-items: center;
    gap: 12px;
    height: 21px;
    font-size: 14.5px;
    color: var(--ink);
  }
  .contacts svg { width: 14px; height: 14px; flex: none; }

  .back-pattern {
    position: absolute;
    inset: 0;
    background: linear-gradient(135deg, var(--gold-light), var(--gold) 50%, var(--gold-deep));
  }
  .back-brand {
    position: absolute;
    left: 420px;
    top: 282px;
    height: 46px;
    display: flex;
    align-items: center;
    gap: 10px;
  }
  .back-brand .brand-dot { background: var(--white); }
  .back-brand .brand-name { color: var(--white); font-size: 22px; }
</style>
</head>
<body>
  <section class="card card-front">
    <div class="front-brand">
      <span class="brand-dot"></span>
      <span class="brand-name">Veloran Cabinets</span>
    </div>
    <div class="front-divider"></div>
    <div class="person">
      <p class="person-name">Mitchell Tarrowby</p>
      <p class="person-role">Craftsman</p>
    </div>
    <ul class="contacts">
      <li>
        <svg viewBox="0 0 14 14" aria-hidden="true"><rect x="1" y="3" width="12" height="8" fill="var(--gold)"/><path d="M1 3 L7 8 L13 3" fill="none" stroke="#fff" stroke-width="1.2"/></svg>
        info@veloranjoinery-example.com.au
      </li>
      <li>
        <svg viewBox="0 0 14 14" aria-hidden="true"><circle cx="7" cy="7" r="6" fill="var(--gold)"/><path d="M1 7 H13 M7 1 C4 4 4 10 7 13 M7 1 C10 4 10 10 7 13" fill="none" stroke="#fff" stroke-width="0.9"/></svg>
        www.veloranjoinery-example.com.au
      </li>
      <li>
        <svg viewBox="0 0 14 14" aria-hidden="true"><circle cx="7" cy="7" r="6" fill="var(--gold)"/></svg>
        @veloran.cabinets
      </li>
    </ul>
  </section>

  <section class="card card-back">
    <div class="back-pattern" role="img" aria-label="Embossed tiled monogram pattern in gold"></div>
    <div class="back-brand">
      <span class="brand-dot"></span>
      <span class="brand-name">Veloran Cabinets</span>
    </div>
  </section>
</body>
</html>
```